DuePath.com website design

We are a collection agency that collects debt from past residents of apartments on behalf of Property Management Companies. We are want to design a 3 page website with - Home - How it Works - Schedule Demo. We'd like a sketch of a skyline showing high rise apartment buildings, houses, shops, etc. We would like for there to be some animation, possibly clouds and the sun slowly moving. Maybe kids playing ball or catch or something like that. Bird flying and landing. An electric car charging (to indicate we are modern). We are looking for a friendly community vibe. The site will also need a button "Property Managers Login". When some comes to the site we would like a pop up that says "Property Managers Click Here/Past Residents Click Here" with a different icon for each that relates to the description. I've included a link to a test site we had designed so feel free to use some of the copy from it. We just aren't happy with the design. On the Home page our tag line should be "Get more payments, faster, from past residents!" and "Digital First, NOT Digital Only". All without transaction fees, we don't get paid unless we get you paid first!
Additional selling points:

24 hour virtual agent and virtual telephone agent so we don't miss any opportunities to GET YOUR MONEY!

Old school collection strategies meet cutting edge technology to create effective work flow algorithms to put the best debt collectors on your accounts with data driven intelligence to determine the best way to get paid.

No Subscription Fees
No Payment Processing Fees
No Software Fees
No Mail, Email or TXT Fees

Inquire about our FIRST PARTY accounts receivable outsourcing. You may qualify for free post move out A/R processing and AI payment negotiator for the low hanging fruit. Don't pay full collection commission when there wasn't a full collection attempt!

For the How it Works page - See the page from our previous design. I will include the link below. Please come up with your own version of this but you can use the copy from this page.

The schedule demo page will be a form that will feed to our CRM that will include:
Name
Email
Company
Title
Phone Number
Number of Units
Tell us how we can help you: (a box for them provide details)

Also include our phone number at the bottom with something like

Here is a link to our previous design test site:
https://brookpreview.net/duepath-new/
I've attached an image of the back end so you can get an idea of the colors we need, I've also included our logo. For the most part we would like most of the site to match the blue colors from our logo, but we do need to incorporate some of the yellow in the images I've attached. Possibly make the buttons on the site the yellow color? Make the sun Match the yellow? I'll leave it up to you.

```html
<!DOCTYPE html>
<html lang="en">
<head>
<meta charset="utf-8">
<title>DuePath.com – Home page concepts</title>
<link href="https://fonts.googleapis.com/css2?family=Jost:wght@400;500;600&family=Poppins:wght@400;500;600;700&display=swap" rel="stylesheet">
<style>
:root{
  --stage:#4b4b4b;
  --navy:#0e3a70;
  --ink:#1b2a4a;
  --cyan:#1bb9c9;
  --cyan-soft:#eaf8fc;
  --royal:#0553b5;
  --yellow:#ffe500;
  --grey-band:#f5f5f7;
  --muted:#5a6478;
  --violet:#8c82d9;
  --white:#ffffff;
}
*{box-sizing:border-box;margin:0;padding:0}
html,body{width:834px;height:1200px;overflow:hidden}
body{background:var(--stage);position:relative;font-family:'Poppins',sans-serif;color:var(--ink)}
.screen{position:absolute;top:33px;width:389px;height:1151px;overflow:hidden;background:var(--white)}
.screen--popup{left:19px}
.screen--plain{left:423px}
.abs{position:absolute}

/* nav */
.nav{left:0;top:0;width:389px;height:35px;background:var(--white);box-shadow:0 2px 6px rgba(27,185,201,.15);z-index:2}
.brand{display:flex;align-items:center;gap:4px;font-family:'Jost',sans-serif;font-weight:600;color:var(--navy);white-space:nowrap}
.brand__dot{width:10px;height:10px;border-radius:50%;background:var(--cyan)}
.nav .brand{left:38px;top:9px;font-size:14px}
.nav__link{top:14px;font-size:5.6px;font-weight:500;color:var(--ink);white-space:nowrap}
.nav__link--active{color:#1aa6d8}
.btn-yellow{background:var(--yellow);color:var(--ink);font-weight:500;display:flex;align-items:center;justify-content:center;white-space:nowrap}
.nav__cta{left:266px;top:9px;width:58px;height:19px;font-size:5.6px}

/* hero */
.hero__title{left:0;top:55px;width:389px;text-align:center;font-size:13px;line-height:17px;font-weight:400;color:var(--ink)}
.hero__title b{font-weight:700}
.hero__art{left:0;top:92px;width:389px;height:180px;border-radius:0 0 50% 50% / 0 0 22px 22px;
  background:linear-gradient(180deg,#ffffff 0%,#dff1fb 20%,#7cc2ee 45%,#3f8ee0 60%,#f6a623 78%,#f5d548 88%,#ffffff 100%)}
.about-bg{left:0;top:262px;width:389px;height:178px;background:linear-gradient(180deg,#e3f6fb,#f4fbfd)}

/* about */
.about__title{left:38px;top:306px;font-family:'Jost',sans-serif;font-size:14px;font-weight:500;color:var(--navy)}
.rule{height:1.5px;background:var(--navy)}
.about__rule{left:38px;top:331px;width:27px}
.about__copy{left:38px;top:342px;width:150px;font-size:4.6px;line-height:9.7px;color:var(--muted)}
.about__copy p+p{margin-top:3px}
.about__cta{left:38px;top:424px;width:45px;height:13px;font-size:5px;font-family:'Jost',sans-serif;font-weight:400}
.about__art{left:194px;top:284px;width:191px;height:162px;border-radius:40% 40% 20% 20%;
  background:radial-gradient(ellipse at 55% 55%,#3b5fd0 0%,#8aa4ef 40%,#f3d24a 62%,rgba(234,248,252,0) 75%)}

/* features */
.features{left:0;top:440px;width:389px;height:177px;background:var(--grey-band)}
.feature{top:478px;width:72px;text-align:center}
.feature__icon{width:38px;height:38px;margin:0 auto;border-radius:50%;border:1px solid var(--violet);background:var(--white);display:flex;align-items:center;justify-content:center}
.feature__title{margin-top:9px;font-family:'Jost',sans-serif;font-size:4.8px;font-weight:500;color:var(--ink);white-space:nowrap}
.feature__text{margin-top:3px;font-family:'Jost',sans-serif;font-size:3.7px;line-height:7.5px;color:var(--muted);white-space:nowrap}
.features__cta{left:166px;top:581px;width:63px;height:20px;font-size:5.8px}

/* how it works */
.how{left:0;top:617px;width:389px;height:182px;background:var(--royal);overflow:hidden}
.how__title{left:0;top:10px;width:389px;text-align:center;font-family:'Jost',sans-serif;font-size:14px;font-weight:500;color:var(--white)}
.how__label{font-size:5.8px;line-height:11px;font-weight:500;color:var(--white);white-space:nowrap}
.how__ring{left:131px;top:105px;width:126px;height:126px;border-radius:50%;background:#dfe8f7}
.how__core{left:149px;top:123px;width:90px;height:90px;border-radius:50%;background:var(--white);display:flex;justify-content:center;padding-top:26px;font-family:'Jost',sans-serif;font-weight:600;font-size:14px;color:var(--navy)}
.how__node{width:25px;height:25px;border-radius:50%;background:var(--white);display:flex;align-items:center;justify-content:center;box-shadow:0 0 0 3px rgba(255,255,255,.25)}

/* contact */
.contact{left:0;top:799px;width:389px;height:238px;background:var(--cyan-soft)}
.contact__title{left:0;top:36px;width:380px;text-align:center;font-family:'Jost',sans-serif;font-size:14px;font-weight:500;color:var(--navy)}
.contact__rule{left:177px;top:58px;width:27px}
.field{height:19px;border-radius:10px;background:var(--white);box-shadow:0 1px 4px rgba(14,58,112,.08);font-size:5px;color:var(--muted);display:flex;align-items:center;padding-left:10px;white-space:nowrap}
.field--area{align-items:flex-start;padding-top:8px;border-radius:8px}
.field--select{justify-content:space-between;padding-right:10px}
.contact__submit{left:260px;top:196px;width:46px;height:18px;font-size:5.5px}

/* footer */
.footer{left:0;top:1037px;width:389px;height:114px;background:linear-gradient(180deg,#123f86 0%,#0f3673 55%,#0b2b5c 100%);color:var(--white)}
.footer .brand{left:36px;top:10px;font-size:14px;color:var(--white)}
.footer .brand__dot{background:var(--white)}
.footer__copy{left:35px;top:38px;width:100px;font-size:4.3px;line-height:9.6px;color:#d5def0}
.footer__head{top:17px;font-family:'Jost',sans-serif;font-size:6.5px;font-weight:500;white-space:nowrap}
.footer__list{left:148px;top:31px;font-size:4.4px;line-height:5.6px;list-style:none;color:#d5def0;white-space:nowrap}
.footer__list li{display:flex;gap:4px;margin-bottom:4.6px}
.footer__list svg{flex:none;margin-top:.3px}
.footer__email{left:269px;top:31px;width:84px;height:14px;background:var(--white);font-size:5px;color:var(--muted);display:flex;align-items:center;padding-left:8px}
.footer__apply{left:269px;top:51px;width:45px;height:13px;font-size:5px}
.footer__legal{left:35px;top:98px;font-size:4.5px;color:#d5def0;white-space:nowrap}
.footer__social{left:320px;top:98px;display:flex;gap:8px}
.footer__social span{width:5px;height:5px;border-radius:50%;background:#9fc2ff}

/* popup state */
.dim{left:0;top:0;width:389px;height:1151px;background:rgba(140,156,178,.5);z-index:5}
.popup{left:35px;top:52px;width:319px;height:232px;border-radius:20px;z-index:6;
  background:linear-gradient(160deg,#ffffff 0%,#f2f5f8 60%,#e9eef3 100%);
  box-shadow:0 0 18px 4px rgba(27,185,201,.45)}
.popup .brand{left:0;width:319px;top:35px;justify-content:center;font-size:32px;gap:10px}
.popup .brand__dot{width:22px;height:22px}
.popup__btn{left:71px;width:177px;height:42px;border-radius:9px;color:var(--white);font-size:12px;font-weight:500;display:flex;align-items:center;justify-content:center;white-space:nowrap}
.popup__btn--managers{top:105px;background:var(--cyan)}
.popup__btn--residents{top:162px;background:var(--navy)}
</style>
</head>
<body>

<!-- ======= Concept A: entry chooser shown over the home page ======= -->
<div class="screen screen--popup">
  <header class="abs nav">
    <div class="abs brand"><span class="brand__dot"></span>DuePath</div>
    <span class="abs nav__link nav__link--active" style="left:168px">HOME</span>
    <span class="abs nav__link" style="left:208px">HOW IT WORKS</span>
    <span class="abs nav__cta btn-yellow">SCHEDULE DEMO</span>
  </header>
  <h1 class="abs hero__title">"Get more payments, faster,<br>from <b>PAST RESIDENTS!"</b></h1>
  <div class="abs about-bg"></div>
  <div class="abs hero__art" role="img" aria-label="Colourful illustrated city skyline with apartment towers, houses, trees, planes and people walking"></div>

  <h2 class="abs about__title">About Us</h2>
  <div class="abs rule about__rule"></div>
  <div class="abs about__copy">
    <p>Lorem ipsum dolor sit amet, consectetur adipiscing elit, sed do eiusmod tempor incididunt ut labore et dolore magna aliqua. Ut enim ad minim veniam, quis nostrud exercitation ullamco lab oris nisi ut aliquip ex ea commodo consequat. Duis aute irure dolor in reprehenderit in voluptate velit esse cillum dolore</p>
    <p>Et harum quidem rerum facilis est et expedita distinctio. Nam liberort tempore, cum soluta nobis est eligendi optio.</p>
  </div>
  <span class="abs about__cta btn-yellow">Get Started</span>
  <div class="abs about__art" role="img" aria-label="Isometric illustration of a city block with towers, chat bubbles and a map pin"></div>

  <section class="abs features"></section>
  <div class="abs feature" style="left:37px">
    <div class="feature__icon"><svg width="16" height="16" viewBox="0 0 16 16" fill="none" stroke="#3a4aa8" stroke-width="1"><circle cx="8" cy="8" r="6"/><path d="M5 8l2 2 4-4"/></svg></div>
    <div class="feature__title">No Subscription Fees</div>
    <div class="feature__text">Duis aute irure dolor in reprehendrit<br>inti voluptate velit esse cillum dolore<br>eu fugiat nulla pariatur.</div>
  </div>
  <div class="abs feature" style="left:120px">
    <div class="feature__icon"><svg width="16" height="16" viewBox="0 0 16 16" fill="none" stroke="#3a4aa8" stroke-width="1"><rect x="3" y="3" width="9" height="11" rx="1"/><path d="M5 6h5M5 8h5M5 10h3"/><circle cx="11.5" cy="11.5" r="2"/></svg></div>
    <div class="feature__title">No Payment Processing Fees</div>
    <div class="feature__text">Duis aute irure dolor in reprehendrit<br>inti voluptate velit esse cillum dolore<br>eu fugiat nulla pariatur.</div>
  </div>
  <div class="abs feature" style="left:201px">
    <div class="feature__icon"><svg width="16" height="16" viewBox="0 0 16 16" fill="none" stroke="#3a4aa8" stroke-width="1"><path d="M4 2h6l3 3v9H4z"/><path d="M6 7h5M6 9h5M6 11h3"/></svg></div>
    <div class="feature__title">No Mail, Email or TXT Fees</div>
    <div class="feature__text">Duis aute irure dolor in reprehendrit<br>inti voluptate velit esse cillum dolore<br>eu fugiat nulla pariatur.</div>
  </div>
  <div class="abs feature" style="left:279px">
    <div class="feature__icon"><svg width="16" height="16" viewBox="0 0 16 16" fill="none" stroke="#3a4aa8" stroke-width="1"><circle cx="8" cy="8" r="6" stroke-dasharray="2 1"/><text x="8" y="10" font-size="5" text-anchor="middle" fill="#3a4aa8" stroke="none" font-family="Poppins,sans-serif">24</text></svg></div>
    <div class="feature__title">24 hour virtual agent</div>
    <div class="feature__text">Duis aute irure dolor in reprehendrit<br>inti voluptate velit esse cillum dolore<br>eu fugiat nulla pariatur.</div>
  </div>
  <span class="abs features__cta btn-yellow">SCHEDULE DEMO</span>

  <section class="abs how">
    <h2 class="abs how__title">How It Works ?</h2>
    <svg class="abs" style="left:0;top:0" width="389" height="182"><circle cx="194" cy="168" r="90" fill="none" stroke="rgba(255,255,255,.45)" stroke-width=".8" stroke-dasharray="3 2"/></svg>
    <div class="abs how__ring"></div>
    <div class="abs how__core">DuePath</div>
    <p class="abs how__label" style="left:134px;top:44px;width:120px;text-align:center">We offer convenient<br>payment platforms</p>
    <p class="abs how__label" style="left:45px;top:86px;width:70px;text-align:right">We contact your past<br>resident before they<br>are delinquent</p>
    <p class="abs how__label" style="left:272px;top:90px;width:100px;text-align:center">Intense collections<br>begins once delinquent</p>
    <p class="abs how__label" style="left:20px;top:146px;width:80px;text-align:center">Transfer accounts<br>to DuePath</p>
    <p class="abs how__label" style="left:268px;top:135px;width:100px;text-align:center">Credit reporting and<br>legal action when<br>possible</p>
    <div class="abs how__node" style="left:182px;top:70px"><svg width="12" height="12" viewBox="0 0 12 12"><circle cx="6" cy="6" r="5" fill="none" stroke="#0553b5"/><text x="6" y="8.3" font-size="6" text-anchor="middle" fill="#0553b5" font-family="Poppins,sans-serif">$</text></svg></div>
    <div class="abs how__node" style="left:122px;top:91px"><svg width="12" height="12" viewBox="0 0 12 12" fill="none" stroke="#0553b5"><rect x="3" y="1" width="6" height="10" rx="1"/><path d="M5 9h2"/></svg></div>
    <div class="abs how__node" style="left:238px;top:91px"><svg width="12" height="12" viewBox="0 0 12 12" fill="none" stroke="#0553b5"><path d="M6 1l5 9H1z"/><path d="M6 4v3M6 8.5v.5"/></svg></div>
    <div class="abs how__node" style="left:97px;top:146px"><svg width="12" height="12" viewBox="0 0 12 12" fill="none" stroke="#0553b5"><rect x="2" y="2.5" width="8" height="5.5"/><path d="M1 10h10"/></svg></div>
    <div class="abs how__node" style="left:266px;top:146px"><svg width="12" height="12" viewBox="0 0 12 12" fill="none" stroke="#0553b5"><rect x="1.5" y="2" width="7" height="8"/><path d="M3 5h4M3 7h3"/><circle cx="9" cy="9" r="2"/></svg></div>
  </section>

  <section class="abs contact">
    <h2 class="abs contact__title">Contact Form</h2>
    <div class="abs rule contact__rule"></div>
    <div class="abs field" style="left:71px;top:81px;width:116px">Name</div>
    <div class="abs field" style="left:195px;top:81px;width:116px">Phone No</div>
    <div class="abs field" style="left:71px;top:106px;width:240px">E-Mail-ID</div>
    <div class="abs field" style="left:72px;top:136px;width:116px">Company</div>
    <div class="abs field" style="left:196px;top:136px;width:116px">Title</div>
    <div class="abs field field--area" style="left:73px;top:165px;width:173px;height:53px">Tell us how we can help you</div>
    <div class="abs field field--select" style="left:251px;top:162px;width:60px">No Of Units <svg width="5" height="3" viewBox="0 0 5 3"><path d="M.5.5l2 2 2-2" fill="none" stroke="#5a6478" stroke-width=".7"/></svg></div>
    <span class="abs contact__submit btn-yellow">SUBMIT</span>
  </section>

  <footer class="abs footer" role="img" aria-label="Footer over a dark blue photographic city skyline">
    <div class="abs brand"><span class="brand__dot"></span>DuePath</div>
    <p class="abs footer__copy">Lorem ipsum dolor sit amet, consectetur adipiscing elit, sed do eiusmod tempor incididunt ut labore et dolore magna aliqua. Ut enim ad minim veniam, quis nostrud</p>
    <h3 class="abs footer__head" style="left:148px">Contact Us</h3>
    <ul class="abs footer__list">
      <li><svg width="5" height="6" viewBox="0 0 5 6" fill="none" stroke="#fff" stroke-width=".6"><path d="M2.5 5.7C1 4 .4 3 .4 2.2a2.1 2.1 0 014.2 0c0 .8-.6 1.8-2.1 3.5z"/><circle cx="2.5" cy="2.2" r=".7"/></svg><span>DuePath,<br>Address Comes Here</span></li>
      <li><svg width="5" height="5" viewBox="0 0 5 5" fill="none" stroke="#fff" stroke-width=".6"><path d="M1 .5l1 1.2-.6.7a3 3 0 001.2 1.2l.7-.6 1.2 1-.5.6C2.2 4.4.6 2.8.5 1z"/></svg><span>Toll-Free: +1800-555-0142</span></li>
      <li><svg width="5" height="4" viewBox="0 0 5 4" fill="none" stroke="#fff" stroke-width=".6"><rect x=".3" y=".3" width="4.4" height="3.4"/><path d="M.3.3l2.2 1.8L4.7.3"/></svg><span>info@duepath.com</span></li>
    </ul>
    <h3 class="abs footer__head" style="left:268px">Subscribe To Newsletter</h3>
    <div class="abs footer__email">Email ID</div>
    <span class="abs footer__apply btn-yellow">APPLY NOW</span>
    <p class="abs footer__legal">Copyright ©2022 DuePath &nbsp;All Rights Reserved.</p>
    <div class="abs footer__social"><span></span><span></span><span></span></div>
  </footer>

  <div class="abs dim"></div>
  <div class="abs popup">
    <div class="abs brand"><span class="brand__dot"></span>DuePath</div>
    <span class="abs popup__btn popup__btn--managers">PROPERTY MANAGERS</span>
    <span class="abs popup__btn popup__btn--residents">PAST RESIDENTS</span>
  </div>
</div>

<!-- ======= Concept B: home page ======= -->
<div class="screen screen--plain">
  <header class="abs nav">
    <div class="abs brand"><span class="brand__dot"></span>DuePath</div>
    <span class="abs nav__link nav__link--active" style="left:168px">HOME</span>
    <span class="abs nav__link" style="left:208px">HOW IT WORKS</span>
    <span class="abs nav__cta btn-yellow">SCHEDULE DEMO</span>
  </header>
  <h1 class="abs hero__title">"Get more payments, faster,<br>from <b>PAST RESIDENTS!"</b></h1>
  <div class="abs about-bg"></div>
  <div class="abs hero__art" role="img" aria-label="Colourful illustrated city skyline with apartment towers, houses, trees, planes and people walking"></div>

  <h2 class="abs about__title">About Us</h2>
  <div class="abs rule about__rule"></div>
  <div class="abs about__copy">
    <p>Lorem ipsum dolor sit amet, consectetur adipiscing elit, sed do eiusmod tempor incididunt ut labore et dolore magna aliqua. Ut enim ad minim veniam, quis nostrud exercitation ullamco lab oris nisi ut aliquip ex ea commodo consequat. Duis aute irure dolor in reprehenderit in voluptate velit esse cillum dolore</p>
    <p>Et harum quidem rerum facilis est et expedita distinctio. Nam liberort tempore, cum soluta nobis est eligendi optio.</p>
  </div>
  <span class="abs about__cta btn-yellow">Get Started</span>
  <div class="abs about__art" role="img" aria-label="Isometric illustration of a city block with towers, chat bubbles and a map pin"></div>

  <section class="abs features"></section>
  <div class="abs feature" style="left:37px">
    <div class="feature__icon"><svg width="16" height="16" viewBox="0 0 16 16" fill="none" stroke="#3a4aa8" stroke-width="1"><circle cx="8" cy="8" r="6"/><path d="M5 8l2 2 4-4"/></svg></div>
    <div class="feature__title">No Subscription Fees</div>
    <div class="feature__text">Duis aute irure dolor in reprehendrit<br>inti voluptate velit esse cillum dolore<br>eu fugiat nulla pariatur.</div>
  </div>
  <div class="abs feature" style="left:120px">
    <div class="feature__icon"><svg width="16" height="16" viewBox="0 0 16 16" fill="none" stroke="#3a4aa8" stroke-width="1"><rect x="3" y="3" width="9" height="11" rx="1"/><path d="M5 6h5M5 8h5M5 10h3"/><circle cx="11.5" cy="11.5" r="2"/></svg></div>
    <div class="feature__title">No Payment Processing Fees</div>
    <div class="feature__text">Duis aute irure dolor in reprehendrit<br>inti voluptate velit esse cillum dolore<br>eu fugiat nulla pariatur.</div>
  </div>
  <div class="abs feature" style="left:201px">
    <div class="feature__icon"><svg width="16" height="16" viewBox="0 0 16 16" fill="none" stroke="#3a4aa8" stroke-width="1"><path d="M4 2h6l3 3v9H4z"/><path d="M6 7h5M6 9h5M6 11h3"/></svg></div>
    <div class="feature__title">No Mail, Email or TXT Fees</div>
    <div class="feature__text">Duis aute irure dolor in reprehendrit<br>inti voluptate velit esse cillum dolore<br>eu fugiat nulla pariatur.</div>
  </div>
  <div class="abs feature" style="left:279px">
    <div class="feature__icon"><svg width="16" height="16" viewBox="0 0 16 16" fill="none" stroke="#3a4aa8" stroke-width="1"><circle cx="8" cy="8" r="6" stroke-dasharray="2 1"/><text x="8" y="10" font-size="5" text-anchor="middle" fill="#3a4aa8" stroke="none" font-family="Poppins,sans-serif">24</text></svg></div>
    <div class="feature__title">24 hour virtual agent</div>
    <div class="feature__text">Duis aute irure dolor in reprehendrit<br>inti voluptate velit esse cillum dolore<br>eu fugiat nulla pariatur.</div>
  </div>
  <span class="abs features__cta btn-yellow">SCHEDULE DEMO</span>

  <section class="abs how">
    <h2 class="abs how__title">How It Works ?</h2>
    <svg class="abs" style="left:0;top:0" width="389" height="182"><circle cx="194" cy="168" r="90" fill="none" stroke="rgba(255,255,255,.45)" stroke-width=".8" stroke-dasharray="3 2"/></svg>
    <div class="abs how__ring"></div>
    <div class="abs how__core">DuePath</div>
    <p class="abs how__label" style="left:134px;top:44px;width:120px;text-align:center">We offer convenient<br>payment platforms</p>
    <p class="abs how__label" style="left:45px;top:86px;width:70px;text-align:right">We contact your past<br>resident before they<br>are delinquent</p>
    <p class="abs how__label" style="left:272px;top:90px;width:100px;text-align:center">Intense collections<br>begins once delinquent</p>
    <p class="abs how__label" style="left:20px;top:146px;width:80px;text-align:center">Transfer accounts<br>to DuePath</p>
    <p class="abs how__label" style="left:268px;top:135px;width:100px;text-align:center">Credit reporting and<br>legal action when<br>possible</p>
    <div class="abs how__node" style="left:182px;top:70px"><svg width="12" height="12" viewBox="0 0 12 12"><circle cx="6" cy="6" r="5" fill="none" stroke="#0553b5"/><text x="6" y="8.3" font-size="6" text-anchor="middle" fill="#0553b5" font-family="Poppins,sans-serif">$</text></svg></div>
    <div class="abs how__node" style="left:122px;top:91px"><svg width="12" height="12" viewBox="0 0 12 12" fill="none" stroke="#0553b5"><rect x="3" y="1" width="6" height="10" rx="1"/><path d="M5 9h2"/></svg></div>
    <div class="abs how__node" style="left:238px;top:91px"><svg width="12" height="12" viewBox="0 0 12 12" fill="none" stroke="#0553b5"><path d="M6 1l5 9H1z"/><path d="M6 4v3M6 8.5v.5"/></svg></div>
    <div class="abs how__node" style="left:97px;top:146px"><svg width="12" height="12" viewBox="0 0 12 12" fill="none" stroke="#0553b5"><rect x="2" y="2.5" width="8" height="5.5"/><path d="M1 10h10"/></svg></div>
    <div class="abs how__node" style="left:266px;top:146px"><svg width="12" height="12" viewBox="0 0 12 12" fill="none" stroke="#0553b5"><rect x="1.5" y="2" width="7" height="8"/><path d="M3 5h4M3 7h3"/><circle cx="9" cy="9" r="2"/></svg></div>
  </section>

  <section class="abs contact">
    <h2 class="abs contact__title">Contact Form</h2>
    <div class="abs rule contact__rule"></div>
    <div class="abs field" style="left:71px;top:81px;width:116px">Name</div>
    <div class="abs field" style="left:195px;top:81px;width:116px">Phone No</div>
    <div class="abs field" style="left:71px;top:106px;width:240px">E-Mail-ID</div>
    <div class="abs field" style="left:72px;top:136px;width:116px">Company</div>
    <div class="abs field" style="left:196px;top:136px;width:116px">Title</div>
    <div class="abs field field--area" style="left:73px;top:165px;width:173px;height:53px">Tell us how we can help you</div>
    <div class="abs field field--select" style="left:251px;top:162px;width:60px">No Of Units <svg width="5" height="3" viewBox="0 0 5 3"><path d="M.5.5l2 2 2-2" fill="none" stroke="#5a6478" stroke-width=".7"/></svg></div>
    <span class="abs contact__submit btn-yellow">SUBMIT</span>
  </section>

  <footer class="abs footer" role="img" aria-label="Footer over a dark blue photographic city skyline">
    <div class="abs brand"><span class="brand__dot"></span>DuePath</div>
    <p class="abs footer__copy">Lorem ipsum dolor sit amet, consectetur adipiscing elit, sed do eiusmod tempor incididunt ut labore et dolore magna aliqua. Ut enim ad minim veniam, quis nostrud</p>
    <h3 class="abs footer__head" style="left:148px">Contact Us</h3>
    <ul class="abs footer__list">
      <li><svg width="5" height="6" viewBox="0 0 5 6" fill="none" stroke="#fff" stroke-width=".6"><path d="M2.5 5.7C1 4 .4 3 .4 2.2a2.1 2.1 0 014.2 0c0 .8-.6 1.8-2.1 3.5z"/><circle cx="2.5" cy="2.2" r=".7"/></svg><span>DuePath,<br>Address Comes Here</span></li>
      <li><svg width="5" height="5" viewBox="0 0 5 5" fill="none" stroke="#fff" stroke-width=".6"><path d="M1 .5l1 1.2-.6.7a3 3 0 001.2 1.2l.7-.6 1.2 1-.5.6C2.2 4.4.6 2.8.5 1z"/></svg><span>Toll-Free: +1800-555-0142</span></li>
      <li><svg width="5" height="4" viewBox="0 0 5 4" fill="none" stroke="#fff" stroke-width=".6"><rect x=".3" y=".3" width="4.4" height="3.4"/><path d="M.3.3l2.2 1.8L4.7.3"/></svg><span>info@duepath.com</span></li>
    </ul>
    <h3 class="abs footer__head" style="left:268px">Subscribe To Newsletter</h3>
    <div class="abs footer__email">Email ID</div>
    <span class="abs footer__apply btn-yellow">APPLY NOW</span>
    <p class="abs footer__legal">Copyright ©2022 DuePath &nbsp;All Rights Reserved.</p>
    <div class="abs footer__social"><span></span><span></span><span></span></div>
  </footer>
</div>

</body>
</html>
```